TA BRAMLEY BUSINESS CARD DESIGN PROJECT

We need to utilize our logo that was expertly created on PixelHarbor and now need to match this with a business card design.

```html
<!DOCTYPE html>
<html lang="en">
<head>
<meta charset="utf-8">
<title>TA BRAMLEY Business Card</title>
<link href="https://fonts.googleapis.com/css2?family=Open+Sans:wght@400;600;700&display=swap" rel="stylesheet">
<style>
  :root {
    --brand-blue: #1257ad;
    --card-black: #111111;
    --card-white: #f2f7fb;
    --plain-white: #ffffff;
    --stage: #e9e6e1;
    --muted-white: #e8e8e8;
  }
  * { box-sizing: border-box; margin: 0; padding: 0; }
  html, body {
    width: 1200px; height: 834px; overflow: hidden;
    background: var(--stage);
    font-family: "Open Sans", Arial, sans-serif;
  }
  .stage {
    position: relative; width: 1200px; height: 834px;
    display: flex; align-items: center; justify-content: center; gap: 40px;
  }
  .card {
    position: relative; width: 520px; height: 297px; overflow: hidden;
    box-shadow: 0 6px 18px rgba(0,0,0,0.18);
  }
  .card-front { background: var(--card-white); }
  .wave { position: absolute; inset: 0; width: 100%; height: 100%; }
  .wave-black { fill: var(--card-black); }
  .wave-line { fill: none; stroke: var(--brand-blue); stroke-width: 4; }
  .contact-block { position: absolute; left: 26px; top: 38px; color: var(--muted-white); }
  .person-name { color: var(--brand-blue); font-weight: 700; font-size: 16px; letter-spacing: 0.3px; }
  .person-title { font-size: 13px; margin-top: 1px; }
  .contact-list { list-style: none; margin-top: 16px; font-size: 11.5px; line-height: 19px; }
  .contact-list li { display: flex; align-items: center; gap: 7px; }
  .contact-icon { width: 10px; height: 10px; fill: var(--brand-blue); flex: none; }
  .address { position: absolute; right: 70px; bottom: 14px; color: var(--muted-white); font-size: 14px; line-height: 19px; }
  .brand { position: absolute; display: flex; align-items: center; gap: 10px; font-weight: 700; letter-spacing: 4px; }
  .brand-mark { display: block; }
  .brand-front { right: 30px; top: 96px; color: var(--brand-blue); font-size: 24px; }
  .brand-front .brand-mark { width: 18px; height: 18px; background: var(--brand-blue); }
  .card-back { background: var(--brand-blue); }
  .brand-back { inset: 0; justify-content: center; color: var(--plain-white); font-size: 38px; }
  .brand-back .brand-mark { width: 28px; height: 28px; background: var(--plain-white); }
</style>
</head>
<body>
<main class="stage">
  <section class="card card-front" aria-label="Business card front">
    <svg class="wave" viewBox="0 0 520 297" preserveAspectRatio="none" aria-hidden="true">
      <path class="wave-black" d="M0,0 L92,0 C192,0 200,100 245,170 C285,228 370,228 520,222 L520,297 L0,297 Z"/>
      <path class="wave-line" d="M96,-4 C204,-4 214,94 257,162 C297,216 374,216 520,210"/>
    </svg>
    <div class="contact-block">
      <p class="person-name">NORA WHITFIELD</p>
      <p class="person-title">Managing Director</p>
      <ul class="contact-list">
        <li><svg class="contact-icon" viewBox="0 0 10 10"><path d="M2,0 L4,2.5 L3,3.6 C3.6,5 5,6.4 6.4,7 L7.5,6 L10,8 L8.6,9.8 C4.5,9.6 0.4,5.5 0.2,1.4 Z"/></svg>123 456 789</li>
        <li><svg class="contact-icon" viewBox="0 0 10 10"><path d="M0,2 H10 V8.5 H0 Z M0.6,2.4 L5,5.6 L9.4,2.4" stroke="#111" stroke-width="0.8"/></svg>info@yourmail.com</li>
        <li><svg class="contact-icon" viewBox="0 0 10 10"><circle cx="5" cy="5" r="5"/></svg>www.yourwebsite.com</li>
      </ul>
    </div>
    <p class="address">Your address, City<br>State, Zip 1234</p>
    <div class="brand brand-front"><span class="brand-mark"></span>TA BRAMLEY</div>
  </section>
  <section class="card card-back" aria-label="Business card back">
    <div class="brand brand-back"><span class="brand-mark"></span>TA BRAMLEY</div>
  </section>
</main>
</body>
</html>
```